female esthetician looking for an impact business card

I an an expert in skin care industry with high experience in NYC.I want my business card to look professional , an impact at first look. I do want a combination between white and gold . I believe the font will be great if is gold.. The Fonts are also important. MIRABELA COSTINA (SKIN CARE BOUTIQUE)

THIS SHOULD BE THE BUSINESS NAME, and should be placed on th eback of the card.
IN front m, the name MIRABELA COSTINA - ESTHETCIAN

BY APPOINTMENTS ONLY: 518.240.7136

Target Market(s)

HIGH END CLIENTELE

Contact Information for Business Card

iT WILL BE on a luxury paper. I neeed the wow feeling

Requirements
Should not have
• pictures

```html
<!DOCTYPE html>
<html lang="en">
<head>
<meta charset="utf-8">
<title>Mirabela Costina – Business Card</title>
<link href="https://fonts.googleapis.com/css2?family=Lato:wght@400;700;900&family=Rokkitt:wght@500;600&display=swap" rel="stylesheet">
<style>
  :root {
    --backdrop: #3a3a3a;
    --card: #111111;
    --pattern-dark: #161616;
    --pattern-light: #222222;
    --gold: #ffc52e;
    --white: #f2f2f2;
    --divider: #4a4a4a;
  }
  * { margin: 0; padding: 0; box-sizing: border-box; }
  html, body { width: 1200px; height: 782px; overflow: hidden; }
  body { background: var(--backdrop); position: relative; font-family: 'Lato', sans-serif; }

  .card {
    position: absolute;
    width: 600px;
    height: 340px;
    background: var(--card);
    overflow: hidden;
    box-shadow: 0 8px 24px rgba(0,0,0,.45);
  }
  .card-back { left: 580px; top: 50px; }
  .card-front { left: 40px; top: 392px; }

  .gold-band {
    position: absolute;
    left: 0; right: 0;
    bottom: 8px;
    height: 9px;
    background: var(--gold);
  }

  /* Back */
  .pattern-field {
    position: absolute;
    inset: 0 0 17px 0;
    background: linear-gradient(135deg, var(--pattern-dark), var(--pattern-light) 50%, var(--pattern-dark));
  }
  .back-mark {
    position: absolute;
    right: 60px; top: 190px;
    display: flex; align-items: center; gap: 10px;
  }
  .back-mark .dot { width: 14px; height: 14px; border-radius: 50%; background: var(--gold); flex: none; }
  .back-mark .brand {
    font-family: 'Rokkitt', serif; font-weight: 600;
    color: var(--gold); font-size: 17px; letter-spacing: 1.5px; line-height: 1.15;
  }
  .back-mark .brand small { display: block; font-size: 12px; letter-spacing: 1.2px; }

  /* Front */
  .identity {
    position: absolute;
    left: 0; top: 70px; width: 320px;
    text-align: center;
  }
  .identity .dot {
    width: 44px; height: 44px; border-radius: 50%;
    background: var(--gold); margin: 0 auto 22px;
  }
  .identity .brand {
    font-family: 'Rokkitt', serif; font-weight: 600;
    color: var(--gold); font-size: 27px; letter-spacing: 2.5px; line-height: 1;
  }
  .identity .tagline {
    font-family: 'Rokkitt', serif; font-weight: 500;
    color: var(--white); font-size: 17px; margin-top: 4px;
  }

  .divider {
    position: absolute;
    left: 335px; top: 90px;
    width: 1px; height: 165px;
    background: var(--divider);
  }

  .contact {
    position: absolute;
    left: 352px; top: 92px;
    color: var(--white);
    text-transform: uppercase;
  }
  .contact .person { color: var(--gold); font-weight: 900; font-size: 19px; letter-spacing: .5px; line-height: 1.1; }
  .contact .role { font-size: 12px; letter-spacing: .5px; margin-bottom: 6px; }
  .contact .appointment { color: var(--gold); font-size: 11px; font-weight: 700; letter-spacing: .6px; line-height: 16px; }
  .contact ul { list-style: none; }
  .contact li { display: flex; align-items: center; gap: 6px; font-size: 13px; line-height: 19px; letter-spacing: .3px; }
  .contact li svg { width: 11px; height: 11px; fill: var(--gold); flex: none; }
  .contact .address { font-size: 13px; line-height: 17px; letter-spacing: .3px; margin-top: 2px; }
</style>
</head>
<body>

  <section class="card card-back">
    <div class="pattern-field" role="img" aria-label="Repeating tonal ornament pattern in dark charcoal"></div>
    <div class="back-mark">
      <span class="dot"></span>
      <span class="brand">MIRABELA COSTINA<small>(SKIN CARE BOUTIQUE)</small></span>
    </div>
    <div class="gold-band"></div>
  </section>

  <section class="card card-front">
    <div class="identity">
      <div class="dot"></div>
      <div class="brand">MIRABELA COSTINA</div>
      <div class="tagline">skin care boutique</div>
    </div>

    <div class="divider"></div>

    <div class="contact">
      <div class="person">Mirabela Costina</div>
      <div class="role">Esthetician</div>
      <div class="appointment">By appointments only</div>
      <ul>
        <li>
          <svg viewBox="0 0 12 12"><path d="M2.5 1h2l1 2.8-1.3.9a6.5 6.5 0 0 0 3.1 3.1l.9-1.3 2.8 1v2A1.5 1.5 0 0 1 9.5 11 8.5 8.5 0 0 1 1 2.5 1.5 1.5 0 0 1 2.5 1z"/></svg>
          518.240.7136
        </li>
        <li>
          <svg viewBox="0 0 12 12"><path d="M0 2h12v1L6 7 0 3z"/><path d="M0 4.2l6 4 6-4V10H0z"/></svg>
          info@mirabelacostina.com
        </li>
        <li>
          <svg viewBox="0 0 12 12"><path d="M6 0a6 6 0 1 0 0 12A6 6 0 0 0 6 0zm0 1.3c.7.8 1.2 2 1.4 3.2H4.6C4.8 3.3 5.3 2.1 6 1.3zM1.4 5.5h2.2c0 1.2.3 2.3.8 3.3a4.7 4.7 0 0 1-3-3.3zm2.2-1H1.4a4.7 4.7 0 0 1 3-3.3c-.5 1-.8 2.1-.8 3.3zm3.8 1c-.2 1.2-.7 2.4-1.4 3.2-.7-.8-1.2-2-1.4-3.2zm1 0h2.2a4.7 4.7 0 0 1-3 3.3c.5-1 .8-2.1.8-3.3zm0-1c0-1.2-.3-2.3-.8-3.3a4.7 4.7 0 0 1 3 3.3z"/></svg>
          www.mirabelacostina.com
        </li>
      </ul>
      <div class="address">72 Laurel Avenue<br>New York, NY 10021</div>
    </div>

    <div class="gold-band"></div>
  </section>

</body>
</html>
```